Lorvex Tilo medical cannibis cultivation company

tag - Tilo rise
Lorvex Tilo medical cannabis cultivation - logo is selected- can we please see bold examples with our selection. We are mainly dealing with medical companies and professionals. We would like to be stand out in the crowd with our designs. Welcome any and all attempts. Thanks

Target Market(s)

Medical and Professional

Industry/Entity Type

Medical And Science

Font styles to use
Sans Serif

Colors

Designer to choose colors to be used in the design.

Requirements
Must have
• Bright colour and be bold- Love the teal and magenta that is currently on the dark background design.
Nice to have
• shading and the 3D affect- The shadowed appearance.
Should not have
• Anything related to illegal activity or un professional manners

```html
<!DOCTYPE html>
<html lang="en">
<head>
<meta charset="utf-8">
<title>Lorvex Tilo — Business Card</title>
<link rel="stylesheet" href="https://fonts.googleapis.com/css2?family=Roboto:wght@400;500;700&display=swap">
<style>
  :root {
    --page: #e6e6e6;
    --card: #000000;
    --teal: #1aa9e0;
    --magenta: #9a3f99;
    --grey: #8a8f94;
    --text: #e8e8e8;
    --band-text: #111111;
  }
  * { margin: 0; padding: 0; box-sizing: border-box; }
  html, body {
    width: 1125px; height: 1200px; overflow: hidden;
    background: var(--page);
    font-family: "Roboto", Arial, sans-serif;
  }
  .canvas { position: relative; width: 1125px; height: 1200px; }
  .card {
    position: absolute; left: 150px; width: 825px; height: 471px;
    background: var(--card); border-radius: 26px; overflow: hidden;
    box-shadow: 0 14px 30px rgba(0,0,0,0.28);
  }
  .card--front { top: 98px; }
  .card--back { top: 631px; }

  .brand { position: absolute; left: 70px; top: 90px; width: 360px; text-align: center; }
  .brand__disc {
    width: 150px; height: 150px; margin: 0 auto 22px;
    border: 6px solid var(--grey); border-radius: 50%;
  }
  .brand__name {
    font-weight: 500; font-size: 50px; line-height: 1; color: var(--teal);
    letter-spacing: 0.5px;
  }
  .brand__tag {
    display: flex; align-items: center; justify-content: center; gap: 8px;
    margin-top: 6px; color: var(--grey); font-size: 20px; letter-spacing: 2px;
    text-transform: uppercase;
  }
  .brand__tag::before, .brand__tag::after {
    content: ""; width: 58px; height: 2px; background: var(--grey);
  }

  .divider {
    position: absolute; left: 451px; top: 78px; width: 2px; height: 270px;
    background: linear-gradient(transparent, #555 20%, #555 80%, transparent);
  }

  .contact { position: absolute; left: 495px; top: 84px; color: var(--text); }
  .contact__name { font-size: 30px; font-weight: 700; color: var(--teal); line-height: 1.1; }
  .contact__role { font-size: 21px; font-weight: 500; color: var(--magenta); margin-bottom: 16px; }
  .contact__address { font-size: 20px; line-height: 25px; margin-bottom: 14px; }
  .contact__list { list-style: none; font-size: 20px; }
  .contact__list li { display: flex; align-items: center; height: 26.5px; }
  .contact__list svg { width: 18px; height: 18px; margin-right: 12px; fill: var(--teal); }

  .band {
    position: absolute; left: 0; top: 406px; width: 100%; height: 41px;
    background: var(--teal); display: flex; align-items: center;
  }
  .band__url {
    margin-left: 134px; font-size: 19px; letter-spacing: 11.5px; color: var(--band-text);
  }
  .band__dot {
    position: absolute; left: 692px; top: 9px; width: 24px; height: 24px;
    border-radius: 50%; background: var(--magenta);
  }

  .back-brand { position: absolute; right: 70px; bottom: 70px; width: 230px; text-align: center; }
  .back-brand__disc {
    width: 124px; height: 124px; margin: 0 auto 10px;
    border: 5px solid var(--grey); border-radius: 50%;
  }
  .back-brand__name { font-size: 22px; font-weight: 500; color: var(--teal); margin-bottom: 8px; }
  .back-brand__url { font-size: 19px; color: var(--text); letter-spacing: 0.3px; }
</style>
</head>
<body>
<main class="canvas">
  <section class="card card--front">
    <div class="brand">
      <div class="brand__disc"></div>
      <div class="brand__name">Lorvex Tilo</div>
      <div class="brand__tag">Tilo Rise</div>
    </div>

    <div class="divider"></div>

    <div class="contact">
      <div class="contact__name">MAREN OSK</div>
      <div class="contact__role">CEO/FOUNDER</div>
      <div class="contact__address">4120 Willowbend Road<br>Fairhaven, Alaska 36012</div>
      <ul class="contact__list">
        <li><svg viewBox="0 0 24 24"><path d="M6.6 10.8a15.1 15.1 0 0 0 6.6 6.6l2.2-2.2c.3-.3.7-.4 1-.2 1.1.4 2.3.6 3.6.6.6 0 1 .4 1 1V20c0 .6-.4 1-1 1A17 17 0 0 1 3 4c0-.6.4-1 1-1h3.5c.6 0 1 .4 1 1 0 1.3.2 2.5.6 3.6.1.3 0 .7-.2 1z"/></svg>555 210 4417</li>
        <li><svg viewBox="0 0 24 24"><path d="M7 1h10a2 2 0 0 1 2 2v18a2 2 0 0 1-2 2H7a2 2 0 0 1-2-2V3a2 2 0 0 1 2-2zm0 3v15h10V4zm5 16.2a1 1 0 1 0 0 .1z"/></svg>555 382 9061</li>
        <li><svg viewBox="0 0 24 24"><path d="M6 2h12v6H6zM3 9h18a2 2 0 0 1 2 2v7h-4v4H5v-4H1v-7a2 2 0 0 1 2-2zm4 8v3h10v-3z"/></svg>555 719 3325</li>
        <li><svg viewBox="0 0 24 24"><path d="M2 5h20v14H2zm2 2v.5l8 5.5 8-5.5V7l-8 5.2z"/></svg>maren@lorvextilo.com</li>
      </ul>
    </div>

    <div class="band">
      <span class="band__url">www.lorvextilorise.com</span>
      <span class="band__dot"></span>
    </div>
  </section>

  <section class="card card--back">
    <div class="back-brand">
      <div class="back-brand__disc"></div>
      <div class="back-brand__name">Lorvex Tilo</div>
      <div class="back-brand__url">www.lorvextilorise.com</div>
    </div>
  </section>
</main>
</body>
</html>
```